Stylish Business Cards Wanted

- DOUBLE SIDED Design Required -

High end, edgy cards for a corporate and personal stylist. Must include logo,
Name: Belinda Harwick
Title: Director and Stylist
telephone : +61 8 7142 5809
email: belinda@theloombriefing.example
website: theloombriefing.example
Tag: Corporate Workwear & Uniform Specialist | Personal Stylist
Would like nice icons for telephone, email, website

Target Market(s)

Businesses wanting stylish uniforms, people wanting stylish wardrobes

Industry/Entity Type

Corporate Workwear Stylist

Contact Information for Business Card

I would like black, white and gold foiling incorporated in the design - possibly a touch of the other colours on my branding guide attached Name: Belinda Harwick Title: Director and Stylist telephone : +61 8 7142 5809 email: belinda@theloombriefing.example website: theloombriefing.example Tag: Corporate Workwear & Uniform Specialist | Personal Stylist Would like nice icons for telephone, email, website

Font styles to use
Other font styles liked:
• Raleway

Colors

Designer to choose colors to be used in the design.

Requirements
Must have
• Gold foil accents

```html
<!DOCTYPE html>
<html lang="en">
<head>
<meta charset="utf-8">
<title>The Loom Briefing – Business Cards</title>
<link rel="stylesheet" href="https://fonts.googleapis.com/css2?family=Montserrat:wght@400;500;700&display=swap">
<style>
  :root {
    --backdrop: #1b1b1b;
    --card-dark: #1f1f1f;
    --card-light: #383838;
    --gold: #e8c25c;
    --white: #ffffff;
  }
  * { box-sizing: border-box; margin: 0; padding: 0; }
  html, body {
    width: 1200px; height: 900px; overflow: hidden;
    background: var(--backdrop);
    font-family: "Montserrat", sans-serif;
    color: var(--white);
  }
  .sheet {
    width: 1200px; height: 900px;
    display: flex; flex-direction: column;
    align-items: center; justify-content: center; gap: 44px;
  }
  .card {
    position: relative;
    width: 672px; height: 384px;
    background: linear-gradient(110deg, var(--card-dark) 35%, var(--card-light) 100%);
    box-shadow: 0 10px 24px rgba(0,0,0,.55);
    overflow: hidden;
  }
  .brand-name {
    font-weight: 500;
    color: var(--white);
    letter-spacing: .04em;
    white-space: nowrap;
  }
  /* front */
  .card-front .brand-name {
    position: absolute; left: 0; right: 0; top: 118px;
    text-align: center; font-size: 46px;
  }
  .tagline {
    position: absolute; left: 0; right: 0; top: 226px;
    text-align: center; font-size: 13px; letter-spacing: .08em;
    color: var(--gold); white-space: nowrap;
  }
  /* back */
  .card-back .brand-name {
    position: absolute; left: 44px; top: 48px; font-size: 30px;
  }
  .holder {
    position: absolute; right: 56px; top: 166px; text-align: right;
  }
  .holder-name {
    font-weight: 700; font-size: 27px; letter-spacing: .05em;
    color: var(--gold); text-transform: uppercase;
  }
  .holder-title { font-size: 17px; margin-top: 4px; }
  .gold-bar {
    position: absolute; right: 22px; top: 190px;
    width: 18px; height: 48px; background: var(--gold);
  }
  .contact-list {
    position: absolute; left: 44px; bottom: 40px;
    list-style: none; display: flex; flex-direction: column; gap: 8px;
  }
  .contact-item {
    display: flex; align-items: center; gap: 12px;
    font-size: 17px; letter-spacing: .02em;
  }
  .contact-icon { width: 16px; height: 16px; fill: var(--gold); flex: none; }
</style>
</head>
<body>
<main class="sheet">
  <section class="card card-front" aria-label="Card front">
    <p class="brand-name">The Loom Briefing</p>
    <p class="tagline">CORPORATE WORKWEAR | UNIFORM SPECIALIST | PERSONAL STYLIST</p>
  </section>

  <section class="card card-back" aria-label="Card back">
    <p class="brand-name">The Loom Briefing</p>

    <div class="holder">
      <p class="holder-name">Belinda Harwick</p>
      <p class="holder-title">Director and Stylist</p>
    </div>
    <span class="gold-bar"></span>

    <ul class="contact-list">
      <li class="contact-item">
        <svg class="contact-icon" viewBox="0 0 24 24" aria-hidden="true">
          <path d="M6.6 10.8a15.1 15.1 0 0 0 6.6 6.6l2.2-2.2a1 1 0 0 1 1-.25 11.4 11.4 0 0 0 3.6.57 1 1 0 0 1 1 1V20a1 1 0 0 1-1 1A17 17 0 0 1 3 4a1 1 0 0 1 1-1h3.5a1 1 0 0 1 1 1c0 1.25.2 2.45.57 3.57a1 1 0 0 1-.25 1z"/>
        </svg>
        +61 8 7142 5809
      </li>
      <li class="contact-item">
        <svg class="contact-icon" viewBox="0 0 24 24" aria-hidden="true">
          <path d="M2 5h20v14H2z M3.5 6.5 12 13l8.5-6.5" stroke="#1f1f1f" stroke-width="1.6"/>
        </svg>
        belinda@theloombriefing.example
      </li>
      <li class="contact-item">
        <svg class="contact-icon" viewBox="0 0 24 24" aria-hidden="true">
          <circle cx="12" cy="12" r="10"/>
          <path d="M2 12h20M12 2c3 3 3 17 0 20M12 2c-3 3-3 17 0 20" stroke="#1f1f1f" stroke-width="1.4" fill="none"/>
        </svg>
        www.theloombriefing.example
      </li>
    </ul>
  </section>
</main>
</body>
</html>
```